Flyer for customer acquisition.

Hello, We are a sportmanagement agency from Germany and we need information flyers for customer acquisition. It should be DinA4 and should have a modern but serious design. I have uploaded a information sheet, where you can find the text and the composition, the flyer should have. I also uploaded Pictures / Images, which you can use. Of course you can use other suitable images. If they are not free, I will buy them later. On the bottom of the flyer there has been the contact information. You will find them in the download section, too. If you have questions, just write me. If I forgot something, I will update the letter :) Thank you very much!
Ich brauche zusätzliche Tage um durchzusehen

```html
<!DOCTYPE html>
<html lang="de">
<head>
<meta charset="utf-8">
<title>TRV-S Nachwuchsförderung – Flyer</title>
<link href="https://fonts.googleapis.com/css2?family=Michroma&family=Open+Sans:wght@400;600;700&family=Roboto+Condensed:wght@700&display=swap" rel="stylesheet">
<style>
  :root {
    --page-bg: #e6e6ea;
    --header-dark: #141618;
    --panel-blue: #0f3a5c;
    --panel-blue-deep: #0a2c48;
    --panel-blue-light: #1a5e8c;
    --accent-yellow: #f5e611;
    --accent-blue: #1e8fe6;
    --footer-dark: #1d1e20;
    --white: #ffffff;
    --fine-text: #c9d6e2;
  }
  * { margin: 0; padding: 0; box-sizing: border-box; }
  html, body { width: 1041px; height: 1200px; overflow: hidden; }
  body { background: var(--page-bg); font-family: "Open Sans", Arial, sans-serif; }

  .flyer-frame {
    position: absolute; left: 110px; top: 24px;
    width: 820px; height: 1152px;
    box-shadow: 0 10px 30px rgba(0,0,0,.25);
  }
  .flyer {
    position: absolute; left: 0; top: 0;
    width: 770px; height: 1082px;
    transform: scale(1.065); transform-origin: 0 0;
    background: var(--panel-blue);
    overflow: hidden;
  }

  /* header */
  .hero {
    position: absolute; left: 0; top: 0; width: 770px; height: 353px;
    background: radial-gradient(ellipse at 55% 40%, #2a2d31 0%, var(--header-dark) 70%);
  }
  .hero-photo-left {
    position: absolute; left: 0; top: 0; width: 320px; height: 347px;
    background: linear-gradient(100deg, #0d0e0f 0%, #5a4a1c 35%, #b08c2c 60%, #3a3018 85%, rgba(20,22,24,0) 100%);
  }
  .hero-divider {
    position: absolute; left: 0; top: 345px; width: 455px; height: 7px;
    background: var(--white);
  }
  .brand-mark {
    position: absolute; z-index: 3; left: 540px; top: 52px; width: 160px;
    display: flex; align-items: center; justify-content: center; gap: 8px;
    color: var(--white); font-family: "Michroma", sans-serif; font-size: 22px;
  }
  .brand-mark .dot { width: 14px; height: 14px; border-radius: 50%; background: var(--white); }
  .hero-title {
    position: absolute; z-index: 3; left: 237px; top: 182px;
    font-family: "Michroma", sans-serif; color: var(--white);
    font-size: 36px; letter-spacing: 1px; line-height: 1;
  }
  .hero-subtitle {
    position: absolute; z-index: 3; left: 237px; top: 230px;
    font-family: "Michroma", sans-serif; color: var(--accent-blue);
    font-size: 16.5px; letter-spacing: 0; line-height: 1; white-space: nowrap;
  }
  .hero-photo-right {
    position: absolute; z-index: 1; left: 515px; top: 125px; width: 250px; height: 360px;
    background: radial-gradient(ellipse at 55% 45%, #2a5fb0 0%, #163a78 45%, rgba(15,58,92,0) 75%);
  }

  /* intro */
  .intro { position: absolute; z-index: 2; left: 23px; top: 375px; }
  .intro-title {
    font-family: "Michroma", sans-serif; color: var(--accent-yellow);
    font-size: 27px; line-height: 1; letter-spacing: .5px;
  }
  .intro-sub {
    margin-top: 9px;
    font-family: "Michroma", sans-serif; color: var(--white);
    font-size: 17.5px; line-height: 1;
  }

  /* services */
  .services-bg {
    position: absolute; left: 0; top: 460px; width: 770px; height: 577px;
    background: linear-gradient(180deg, var(--panel-blue) 0%, var(--panel-blue-deep) 40%, var(--panel-blue-light) 100%);
  }
  .service { position: absolute; z-index: 2; left: 0; width: 770px; height: 80px; }
  .service-icon {
    position: absolute; left: 0; top: 0; width: 70px; height: 75px;
    background: var(--accent-yellow);
    display: flex; align-items: center; justify-content: center;
  }
  .service-icon::after {
    content: ""; position: absolute; right: -7px; top: 30px;
    border-left: 7px solid var(--accent-yellow);
    border-top: 8px solid transparent; border-bottom: 8px solid transparent;
  }
  .service-icon svg { width: 34px; height: 34px; }
  .service-heading {
    position: absolute; left: 81px; top: -2px;
    font-family: "Roboto Condensed", sans-serif; font-weight: 700;
    color: var(--accent-yellow); font-size: 17px; line-height: 20px;
    padding-bottom: 2px; padding-right: 84px;
    border-bottom: 2px solid var(--white);
  }
  .service-text {
    position: absolute; left: 81px; top: 30px; width: 655px;
    color: var(--white); font-size: 15px; line-height: 21px;
  }

  .footnotes {
    position: absolute; z-index: 2; left: 30px; top: 988px; width: 710px;
    text-align: center; color: var(--fine-text); font-size: 8.3px; line-height: 12px;
  }
  .footnotes p + p { margin-top: 5px; }

  /* contact bar */
  .contact-bar {
    position: absolute; z-index: 2; left: 0; top: 1037px; width: 770px; height: 45px;
    background: var(--footer-dark);
    display: flex; align-items: center; justify-content: center;
    color: var(--white); font-weight: 700; font-size: 16.5px;
  }
  .contact-item { display: flex; align-items: center; gap: 8px; padding: 0 38px; }
  .contact-item + .contact-item { border-left: 1px solid #bfbfbf; }
  .contact-item svg { width: 15px; height: 15px; }
</style>
</head>
<body>
<div class="flyer-frame">
  <div class="flyer">

    <header class="hero">
      <div class="hero-photo-left" role="img" aria-label="Foto: Jugendspieler im gelben Trikot mit der Nummer 10, von hinten, jubelnd"></div>
      <div class="brand-mark"><span class="dot"></span>TRV</div>
      <h1 class="hero-title">TRV-S</h1>
      <p class="hero-subtitle">NACHWUCHSFÖRDERUNG</p>
      <div class="hero-divider"></div>
    </header>

    <div class="services-bg"></div>
    <div class="hero-photo-right" role="img" aria-label="Foto: Fußballspieler im blauen Trikot kniend beim Torjubel mit Ball"></div>

    <section class="intro">
      <h2 class="intro-title">WIR BEGLEITEN DICH</h2>
      <p class="intro-sub">AUF DEINEM WEG ZUM PROFI</p>
    </section>

    <section class="service" style="top:463px">
      <div class="service-icon">
        <svg viewBox="0 0 34 34" fill="none" stroke="#1a1a1a" stroke-width="1.6"><circle cx="11" cy="9" r="5"/><path d="M8 9l2 2 4-4"/><path d="M3 30v-5a6 6 0 0 1 12 0v5z"/><rect x="20" y="22" width="3" height="8"/><rect x="25" y="18" width="3" height="12"/><rect x="30" y="14" width="3" height="16"/><path d="M19 14l5-5 4 3 5-6"/></svg>
      </div>
      <h3 class="service-heading">KARRIEREPLANUNG</h3>
      <p class="service-text">Wir haben deine Karriere im Blick! In enger Absprache mit deinen Eltern und dir leiten wir die richtigen Maßnahmen und Schritte ein, um dein Ziel „Profifußballer" zu realisieren.</p>
    </section>

    <section class="service" style="top:549px">
      <div class="service-icon">
        <svg viewBox="0 0 34 34" fill="none" stroke="#1a1a1a" stroke-width="1.8"><path d="M6 18v-3a11 11 0 0 1 22 0v3"/><rect x="4" y="16" width="5" height="9" rx="2"/><rect x="25" y="16" width="5" height="9" rx="2"/><path d="M27 25c0 4-4 6-9 6"/><circle cx="17" cy="17" r="6"/></svg>
      </div>
      <h3 class="service-heading">STÄNDIGER ANSPRECHPARTNER</h3>
      <p class="service-text">Egal um welchen Themen es sich handelt, wir sind für dich da! Ein vertrauensvolles un freundschaftliches Verhältnis ist uns besonders wichtig.</p>
    </section>

    <section class="service" style="top:634px">
      <div class="service-icon">
        <svg viewBox="0 0 34 34" fill="none" stroke="#1a1a1a" stroke-width="1.6"><path d="M17 5v24M10 30h14M6 9h22"/><path d="M8 9l-4 10h8zM26 9l-4 10h8z"/><path d="M4 19a4 3 0 0 0 8 0M22 19a4 3 0 0 0 8 0"/></svg>
      </div>
      <h3 class="service-heading">RECHTSBERATUNG / VERTRAGSRECHT</h3>
      <p class="service-text">Juristendeutsch und Kleingedrucktes? Kein Problem! Wir helfen dir den Durchblick zu behalten und holen immer das Beste für dich raus.</p>
    </section>

    <section class="service" style="top:720px">
      <div class="service-icon">
        <svg viewBox="0 0 34 34" fill="none" stroke="#1a1a1a" stroke-width="1.8"><circle cx="17" cy="17" r="13"/><path d="M17 11l5 4-2 6h-6l-2-6z" fill="#1a1a1a"/><path d="M17 11V4M22 15l7-2M20 21l4 6M14 21l-4 6M12 15l-7-2"/></svg>
      </div>
      <h3 class="service-heading">AUSRÜSTUNG</h3>
      <p class="service-text">Wir besorgen dir deine Ausrüstung! Unsere Beziehungen zu den großen Sportartikelherstellern ermöglichen den Abschluss von Ausrüsterverträgen*.</p>
    </section>

    <section class="service" style="top:806px">
      <div class="service-icon">
        <svg viewBox="0 0 34 34" fill="none" stroke="#1a1a1a" stroke-width="1.8"><path d="M17 3l12 5v9c0 7-5 12-12 14C10 29 5 24 5 17V8z"/><path d="M17 12c3 3 4 5 4 8a4 4 0 0 1-8 0c0-2 1-3 2-4 0 2 1 3 2 3 0-3 0-5 0-7z"/></svg>
      </div>
      <h3 class="service-heading">VORSORGE</h3>
      <p class="service-text">Verletzungen gehören leider zum Fußball dazu. Wir sichern dich ab, indem wir eine private Zusatzkrankenversicherung für dich abschließen.</p>
    </section>

    <section class="service" style="top:891px">
      <div class="service-icon">
        <svg viewBox="0 0 34 34" fill="none" stroke="#1a1a1a" stroke-width="1.6"><circle cx="17" cy="17" r="3"/><circle cx="6" cy="6" r="2.5"/><circle cx="28" cy="6" r="2.5"/><circle cx="6" cy="28" r="2.5"/><circle cx="28" cy="28" r="2.5"/><circle cx="17" cy="4" r="2"/><path d="M8 8l7 7M26 8l-7 7M8 26l7-7M26 26l-7-7M17 6v8"/></svg>
      </div>
      <h3 class="service-heading">KOOPERATIONSPARTNER NETZWERK</h3>
      <p class="service-text">Kooperationspartner/Netzwerk Ob Entscheidungsträger oder Experte, wir kennen die richtigen Leute. Zusätzlich bieten wir dir eine große Bandbreite an Leistungen, die du jederzeit in Anspruch nehmen kannst*</p>
    </section>

    <div class="footnotes">
      <p>*Die Entscheidung über das Zustandekommen eines Ausrüstervertrags obliegt dem jeweiligen Sportartikelhersteller. Ist ein Abschluss aktuell nicht möglich, erhältst du von uns 2x pro Saison neue Fußballschuhe sowie weitere Ausrüstungsgegenstände.</p>
      <p>**Personal Training, Athletik-Training, Ernährungsberatung, Sportpsychologische Betreuung, uvm.</p>
    </div>

    <footer class="contact-bar">
      <div class="contact-item">
        <svg viewBox="0 0 16 16" fill="none" stroke="#fff" stroke-width="1.4"><circle cx="8" cy="8" r="7"/><rect x="4.5" y="5.5" width="7" height="5"/><path d="M4.5 5.5L8 8.5l3.5-3"/></svg>
        info@trv-s.de
      </div>
      <div class="contact-item">
        <svg viewBox="0 0 16 16" fill="none" stroke="#fff" stroke-width="1.3"><circle cx="8" cy="8" r="7"/><ellipse cx="8" cy="8" rx="3" ry="7"/><path d="M1 8h14M2.5 4.5h11M2.5 11.5h11"/></svg>
        www.trv-s.de
      </div>
      <div class="contact-item">
        <svg viewBox="0 0 16 16" fill="none" stroke="#fff" stroke-width="1.4"><path d="M3 1.5l3 3-1.5 2a9 9 0 0 0 5 5l2-1.5 3 3-2 2C6 14 2 10 1 3.5z"/></svg>
        07000/4815162
      </div>
    </footer>

  </div>
</div>
</body>
</html>
```